Stationary Set Rebrand for Brennick

We are a Canadian Distribution and Service Company that was established in 1969. Over the past 5 decades we have expanded our business and have warehouses across Canada. We specialize in adhesive tapes, adhesives, films, safety, warehouse, shipping, janitorial and packaging supplies.

We have updated our logo design and would like a new corporate branding identity that includes a new fresh Stationary Set (Business Cards, Letterhead, Letterhead MS Word, Envelope, Presentation Folders, Email Signatures, Notepad Covers, etc.)

Target Market(s)

Industrial Business Sector

Font styles to use
Sans Serif

Colors
0054AA
0677BA
7BADD7
CADEEF
E8F1F8
0094D4
00A9DD
6FCCEA
C7EBF8
E9F6FB
00AB8E
00BBA5
67D7C9
C6EFE9
E9F9F6
EB3D1F
EC4F4E
F09395
F8D3D4
FCEDEE

Requirements
Should not have
• Colors not too light, darker colours preferred

```html
<!DOCTYPE html>
<html lang="en">
<head>
<meta charset="utf-8">
<title>Brennick Stationery Set</title>
<link href="https://fonts.googleapis.com/css2?family=Lato:ital,wght@0,400;0,700;0,900;1,700&display=swap" rel="stylesheet">
<style>
:root{
  --ink:#1b1b1b;
  --red:#c8102e;
  --paper:#ffffff;
  --backdrop:#dcdde0;
  --floor:#e6e6e7;
  --rule:#b8b8b8;
  --muted:#6d6d6d;
  --faint:#ececec;
}
*{margin:0;padding:0;box-sizing:border-box}
html,body{width:1039px;height:1200px;overflow:hidden}
body{font-family:"Lato",Arial,sans-serif;color:var(--ink);position:relative;background:var(--floor)}
.backdrop{position:absolute;left:0;top:0;width:1039px;height:818px;background:var(--backdrop)}
.piece{position:absolute;background:var(--paper);box-shadow:0 2px 5px rgba(0,0,0,.18);overflow:hidden}
.abs{position:absolute}
.mark{font-weight:900;color:var(--ink);line-height:1;white-space:nowrap;letter-spacing:-.01em}
.mark::after{content:"";display:inline-block;width:.28em;height:.28em;background:var(--red);margin-left:.12em;vertical-align:baseline}
.mark.on-dark{color:#fff}
.tag{font-weight:700;color:var(--ink);white-space:nowrap;line-height:1}
.tag.on-dark{color:#fff}
.contact{border-left:1px solid var(--red);padding-left:4px;line-height:1.45;white-space:nowrap}
.contact .ic{display:inline-block;vertical-align:middle;margin-right:2px}
.ic{fill:var(--red)}
/* business card */
.card{border-radius:8px}
.card-back{background:var(--ink)}
.person{font-weight:900;font-size:10px}
.role{color:var(--red);font-size:7.5px}
.card .contact{font-size:7.5px}
/* letterhead */
.letter-body{font-size:3.9px;line-height:6px;color:#7a7a7a;text-align:justify}
.letter-body p{margin-bottom:6px}
/* invoice */
.inv-table{position:absolute;border-collapse:collapse;font-size:4px;table-layout:fixed}
.inv-table th{font-weight:700;color:#fff;height:10px;text-align:center}
.inv-table td{border:.5px solid #d3d3d3;text-align:center;height:10.8px}
.head-black th{background:var(--ink)}
.head-black th:first-child{text-align:left;padding-left:2px}
.head-red th{background:var(--red)}
.totals td{text-align:left;padding-left:2px;height:10px}
.red-label{color:var(--red);font-weight:700}
.terms{font-size:4px;line-height:6.4px}
/* notebook */
.ruled{border-bottom:.6px solid #9a9a9a;position:absolute;height:0}
.cover-dark{background:var(--ink)}
</style>
</head>
<body>
<svg width="0" height="0" style="position:absolute">
  <symbol id="i-phone" viewBox="0 0 10 10"><path d="M1 3c0-1 1-2 2-2h4c1 0 2 1 2 2v1H7V3H3v1H1zM2 5h6l1 4H1z"/></symbol>
  <symbol id="i-mail" viewBox="0 0 10 10"><path d="M0 2h10v6H0zM1 3l4 3 4-3v-.2H1z" fill-rule="evenodd"/></symbol>
  <symbol id="i-web" viewBox="0 0 10 10"><circle cx="5" cy="5" r="4.5"/><path d="M.5 5h9M5 .5v9" stroke="#fff" stroke-width=".8"/></symbol>
</svg>

<div class="backdrop"></div>

<!-- Business card front -->
<section class="piece card" style="left:60px;top:78px;width:269px;height:157px">
  <div class="abs mark" style="left:19px;top:60px;font-size:23px">Brennick</div>
  <div class="abs tag" style="left:19px;top:86px;font-size:5.6px">Tape and Packaging Specialists</div>
  <div class="abs" style="left:142px;top:38px;width:1px;height:80px;background:var(--red)"></div>
  <div class="abs person" style="left:155px;top:37px">MARCUS DELANEY</div>
  <div class="abs role" style="left:155px;top:50px">Founder &amp; CEO</div>
  <div class="abs" style="left:155px;top:65px;font-size:7.5px;line-height:10.5px">28-710 Cedar Ridge Rd<br>Guelph, ON N1K 4T2</div>
  <div class="abs" style="left:155px;top:89px;font-size:7.5px;line-height:10.5px;white-space:nowrap">
    <svg class="ic" width="6" height="6"><use href="#i-phone"/></svg> 548-555-0193<br>
    <svg class="ic" width="6" height="6"><use href="#i-mail"/></svg> info@brennicksupply.com<br>
    <svg class="ic" width="6" height="6"><use href="#i-web"/></svg> www.brennicksupply.com
  </div>
</section>

<!-- Business card back -->
<section class="piece card card-back" style="left:61px;top:258px;width:270px;height:157px">
  <div class="abs mark on-dark" style="left:48px;top:52px;font-size:38px">Brennick</div>
  <div class="abs tag on-dark" style="left:48px;top:94px;font-size:9px">Tape and Packaging Specialists</div>
</section>

<!-- Letterhead -->
<section class="piece" style="left:347px;top:77px;width:249px;height:353px">
  <div class="abs mark" style="left:22px;top:22px;font-size:15px">Brennick</div>
  <div class="abs tag" style="left:22px;top:38px;font-size:4px">Tape and Packaging Specialists</div>
  <div class="abs contact" style="left:171px;top:16px;font-size:4.4px">
    28-710 Cedar Ridge Rd<br>Guelph, ON N1K 4T2<br>
    <svg class="ic" width="4" height="4"><use href="#i-phone"/></svg>548-555-0193<br>
    <svg class="ic" width="4" height="4"><use href="#i-mail"/></svg>info@brennicksupply.com<br>
    <svg class="ic" width="4" height="4"><use href="#i-web"/></svg>www.brennicksupply.com
  </div>
  <div class="abs" style="left:22px;top:80px;font-size:5px;font-weight:700">Dear. Mrs Alana Reid</div>
  <div class="abs" style="left:22px;top:87px;font-size:3.6px;font-weight:700">Chief Director</div>
  <div class="abs" style="right:22px;top:86px;font-size:3.8px;color:var(--muted)">Date: 16-October-2025</div>
  <div class="abs letter-body" style="left:22px;top:104px;width:206px">
    <p>Thank you for choosing our team as your partner for tape, adhesive and packaging supply. Since 1969 we have served industrial customers across Canada from warehouses placed close to the sites they run. This letter confirms the details of the supply agreement we discussed last week, including product ranges, delivery windows and the service contacts for your account. Our team will review stock levels with your buyers each month and adjust orders to match production. Pricing remains fixed for the first twelve months, with volume breaks applied automatically at each invoice. Safety, janitorial and warehouse items can be added to the same order at any time without a new contract. Please share the agreement with your purchasing and receiving staff so that deliveries are checked in smoothly.</p>
    <p>Our account managers visit each site twice a year to walk the floor, check how products perform on your lines and suggest changes that save time or material. If a tape fails to hold or a film tears during wrapping, call us and we will send a specialist within two working days. Samples of new products are free for approved accounts, and we will gladly run trials alongside your current supplies before you switch.</p>
    <p>We look forward to working with you. Reach out to the office above with any questions about this agreement, and our team will reply the same business day.</p>
  </div>
  <div class="abs" role="img" aria-label="Handwritten signature" style="left:22px;top:240px;width:54px;height:14px;background:linear-gradient(90deg,#e6e6e6,#f4f4f4)"></div>
  <div class="abs" style="left:22px;top:262px;font-size:5px;font-weight:700">Daniel Moore</div>
  <div class="abs" style="left:22px;top:269px;font-size:3.6px;color:var(--muted)">Chief Director</div>
</section>

<!-- Envelope front -->
<section class="piece" style="left:619px;top:77px;width:356px;height:171px">
  <div class="abs mark" style="left:16px;top:15px;font-size:19px">Brennick</div>
  <div class="abs tag" style="left:16px;top:35px;font-size:5px">Tape and Packaging Specialists</div>
  <div class="abs" style="left:16px;top:42px;font-size:5.6px;line-height:7px">28-710 Cedar Ridge Rd<br>Guelph, ON N1K 4T2</div>
</section>

<!-- Envelope back -->
<section class="piece" style="left:619px;top:260px;width:356px;height:171px">
  <svg class="abs" style="left:0;top:0" width="356" height="64" viewBox="0 0 356 64">
    <path d="M0 0H356L334 30Q326 38 312 40L178 61L44 40Q30 38 22 30Z" fill="var(--ink)"/>
  </svg>
  <div class="abs mark on-dark" style="left:143px;top:16px;font-size:15px">Brennick</div>
  <div class="abs tag on-dark" style="left:143px;top:32px;font-size:4px">Tape and Packaging Specialists</div>
</section>

<!-- Invoice -->
<section class="piece" style="left:71px;top:440px;width:248px;height:352px">
  <div class="abs mark" style="left:24px;top:20px;font-size:16px">Brennick</div>
  <div class="abs tag" style="left:24px;top:38px;font-size:4px">Tape and Packaging Specialists</div>
  <div class="abs contact" style="left:173px;top:15px;font-size:4.4px">
    28-710 Cedar Ridge Rd<br>Guelph, ON N1K 4T2<br>
    <svg class="ic" width="4" height="4"><use href="#i-phone"/></svg>548-555-0193<br>
    <svg class="ic" width="4" height="4"><use href="#i-mail"/></svg>info@brennicksupply.com<br>
    <svg class="ic" width="4" height="4"><use href="#i-web"/></svg>www.brennicksupply.com
  </div>
  <div class="abs" style="left:27px;top:58px;font-size:9.5px;font-weight:700;font-style:italic">Invoice</div>
  <table class="inv-table head-black" style="left:23px;top:88px;width:206px">
    <colgroup><col style="width:58px"><col style="width:38px"><col style="width:38px"><col style="width:38px"><col style="width:34px"></colgroup>
    <tr><th>Bill To:</th><th>Due Date</th><th>Date Issued</th><th>Invoice Number</th><th>Amount Due</th></tr>
    <tr><td></td><td>10/01/2023</td><td>01/01/2023</td><td>Inv- 0215</td><td>$1528.00</td></tr>
  </table>
  <table class="inv-table head-red" style="left:23px;top:123px;width:206px">
    <colgroup><col style="width:16px"><col style="width:95px"><col style="width:32px"><col style="width:28px"><col style="width:35px"></colgroup>
    <tr><th>SL NO</th><th>DESCRIPTION</th><th>QUANTITY</th><th>RATE</th><th>AMOUNT</th></tr>
    <tr><td></td><td></td><td></td><td></td><td></td></tr>
    <tr><td></td><td></td><td></td><td></td><td></td></tr>
    <tr><td></td><td></td><td></td><td></td><td></td></tr>
    <tr><td></td><td></td><td></td><td></td><td></td></tr>
    <tr><td></td><td></td><td></td><td></td><td></td></tr>
    <tr><td></td><td></td><td></td><td></td><td></td></tr>
    <tr><td></td><td></td><td></td><td></td><td></td></tr>
    <tr><td></td><td></td><td></td><td></td><td></td></tr>
    <tr><td></td><td></td><td></td><td></td><td></td></tr>
    <tr><td></td><td></td><td></td><td></td><td></td></tr>
  </table>
  <table class="inv-table totals" style="left:166px;top:242px;width:63px">
    <colgroup><col style="width:28px"><col style="width:35px"></colgroup>
    <tr><td class="red-label">Sub Total</td><td></td></tr>
    <tr><td>Discount</td><td></td></tr>
    <tr><td>Tax</td><td></td></tr>
    <tr><td>Total</td><td></td></tr>
    <tr><td class="red-label">Total Due</td><td></td></tr>
  </table>
  <div class="abs terms" style="left:23px;top:248px">
    <span class="red-label">Terms</span><br>
    Please pay within 5 working Days using the following bank details:<br>
    <span style="display:block;height:4px"></span>
    Bank Name:<br>Account Number:<br>Routing Number:<br>Account Name:
  </div>
  <div class="abs red-label" style="left:22px;top:300px;font-size:4.4px">Thank you for your Business!</div>
</section>

<!-- Notebook cover -->
<section class="piece cover-dark" style="left:369px;top:494px;width:194px;height:274px;border-radius:3px">
  <div class="abs mark on-dark" style="left:47px;top:121px;font-size:24px">Brennick</div>
  <div class="abs tag on-dark" style="left:47px;top:147px;font-size:5.6px">Tape and Packaging Specialists</div>
</section>
<svg class="abs" style="left:358px;top:498px" width="26" height="268" viewBox="0 0 26 268">
  <defs><pattern id="coil" width="26" height="6.7" patternUnits="userSpaceOnUse"><ellipse cx="13" cy="3.3" rx="11" ry="2" fill="none" stroke="#8e8e8e" stroke-width="1.1"/></pattern></defs>
  <rect width="26" height="268" fill="url(#coil)"/>
</svg>

<!-- Notebook open -->
<section class="piece" style="left:589px;top:492px;width:191px;height:274px">
  <div class="abs mark" style="left:18px;top:14px;font-size:13px">Brennick</div>
  <div class="abs tag" style="left:18px;top:28px;font-size:3.4px">Tape and Packaging Specialists</div>
  <div class="abs" style="left:141px;top:34px;font-size:3.8px;color:var(--muted)">Date:......./......./.........</div>
  <div class="ruled" style="left:18px;right:16px;top:48px"></div><div class="ruled" style="left:18px;right:16px;top:59px"></div><div class="ruled" style="left:18px;right:16px;top:70px"></div><div class="ruled" style="left:18px;right:16px;top:81px"></div><div class="ruled" style="left:18px;right:16px;top:92px"></div><div class="ruled" style="left:18px;right:16px;top:103px"></div><div class="ruled" style="left:18px;right:16px;top:114px"></div><div class="ruled" style="left:18px;right:16px;top:125px"></div><div class="ruled" style="left:18px;right:16px;top:136px"></div><div class="ruled" style="left:18px;right:16px;top:147px"></div><div class="ruled" style="left:18px;right:16px;top:158px"></div><div class="ruled" style="left:18px;right:16px;top:169px"></div><div class="ruled" style="left:18px;right:16px;top:180px"></div><div class="ruled" style="left:18px;right:16px;top:191px"></div><div class="ruled" style="left:18px;right:16px;top:202px"></div><div class="ruled" style="left:18px;right:16px;top:213px"></div><div class="ruled" style="left:18px;right:16px;top:224px"></div><div class="ruled" style="left:18px;right:16px;top:235px"></div><div class="ruled" style="left:18px;right:16px;top:246px"></div>
</section>
<section class="piece" style="left:788px;top:492px;width:191px;height:274px">
  <div class="abs mark" style="left:14px;top:14px;font-size:13px">Brennick</div>
  <div class="abs tag" style="left:14px;top:28px;font-size:3.4px">Tape and Packaging Specialists</div>
  <div class="abs" style="left:137px;top:34px;font-size:3.8px;color:var(--muted)">Date:......./......./.........</div>
  <div class="ruled" style="left:14px;right:19px;top:48px"></div><div class="ruled" style="left:14px;right:19px;top:59px"></div><div class="ruled" style="left:14px;right:19px;top:70px"></div><div class="ruled" style="left:14px;right:19px;top:81px"></div><div class="ruled" style="left:14px;right:19px;top:92px"></div><div class="ruled" style="left:14px;right:19px;top:103px"></div><div class="ruled" style="left:14px;right:19px;top:114px"></div><div class="ruled" style="left:14px;right:19px;top:125px"></div><div class="ruled" style="left:14px;right:19px;top:136px"></div><div class="ruled" style="left:14px;right:19px;top:147px"></div><div class="ruled" style="left:14px;right:19px;top:158px"></div><div class="ruled" style="left:14px;right:19px;top:169px"></div><div class="ruled" style="left:14px;right:19px;top:180px"></div><div class="ruled" style="left:14px;right:19px;top:191px"></div><div class="ruled" style="left:14px;right:19px;top:202px"></div><div class="ruled" style="left:14px;right:19px;top:213px"></div><div class="ruled" style="left:14px;right:19px;top:224px"></div><div class="ruled" style="left:14px;right:19px;top:235px"></div><div class="ruled" style="left:14px;right:19px;top:246px"></div>
</section>
<svg class="abs" style="left:773px;top:496px" width="22" height="268" viewBox="0 0 22 268">
  <defs><pattern id="coil-open" width="22" height="12" patternUnits="userSpaceOnUse"><ellipse cx="11" cy="6" rx="9" ry="2.2" fill="none" stroke="#8e8e8e" stroke-width="1.2"/></pattern></defs>
  <rect width="22" height="268" fill="url(#coil-open)"/>
</svg>

<!-- Presentation folder outside -->
<section class="piece cover-dark" style="left:80px;top:880px;width:180px;height:240px">
  <div class="abs mark on-dark" style="left:16px;top:170px;font-size:19px">Brennick</div>
  <div class="abs tag on-dark" style="left:16px;top:191px;font-size:4.8px">Tape and Packaging Specialists</div>
  <div class="abs" style="left:16px;top:199px;width:148px;height:.8px;background:var(--red)"></div>
  <div class="abs" style="left:16px;top:203px;font-size:4.8px;color:#fff;line-height:7px;white-space:nowrap">28-710 Cedar Ridge Rd, Guelph, ON N1K 4T2<br>
    <svg class="ic" width="4" height="4"><use href="#i-phone"/></svg> 548-555-0193 &nbsp;
    <svg class="ic" width="4" height="4"><use href="#i-mail"/></svg> info@brennicksupply.com &nbsp;
    <svg class="ic" width="4" height="4"><use href="#i-web"/></svg> www.brennicksupply.com</div>
</section>
<section class="piece" style="left:260px;top:880px;width:180px;height:240px">
  <div class="abs mark" style="left:28px;top:94px;font-size:24px">Brennick</div>
  <div class="abs tag" style="left:28px;top:121px;font-size:6px">Tape and Packaging Specialists</div>
  <div class="abs" style="left:0;right:0;top:222px;text-align:center;font-size:4.8px">www.brennicksupply.com</div>
</section>

<!-- Presentation folder inside -->
<section class="piece" style="left:599px;top:880px;width:180px;height:240px">
  <div class="abs cover-dark" style="left:0;right:0;bottom:0;height:76px;border-radius:10px 10px 0 0"></div>
  <div class="abs mark on-dark" style="left:36px;top:193px;font-size:19px">Brennick</div>
  <div class="abs tag on-dark" style="left:36px;top:214px;font-size:4.6px">Tape and Packaging Specialists</div>
</section>
<section class="piece" style="left:781px;top:880px;width:180px;height:240px">
  <div class="abs cover-dark" style="left:0;right:0;bottom:0;height:76px"></div>
  <div class="abs" style="left:60px;top:178px;width:70px;height:41px;background:var(--paper);border-radius:3px">
    <div class="abs mark" style="left:4px;top:17px;font-size:6.5px">Brennick</div>
    <div class="abs" style="left:37px;top:8px;width:.5px;height:26px;background:var(--red)"></div>
    <div class="abs" style="left:40px;top:8px;font-size:2.6px;line-height:3.4px;white-space:nowrap"><b>MARCUS DELANEY</b><br><span style="color:var(--red)">Founder &amp; CEO</span><br>28-710 Cedar Ridge Rd<br>Guelph, ON N1K 4T2<br>548-555-0193<br>info@brennicksupply.com</div>
  </div>
</section>
</body>
</html>
```